MES Modul-Struktur grafisch veranschaulichen
Zielgruppe
Wir sind Software-Hersteller. Thema 'MES'. Unsere Kunden sind Produktionsunternehmen.
Mit einem MES (Manufacturing Execution System) werden Produktionsprozesse überwacht, geplant, gesteuert und optimiert. Allgemein geht es darum, die Produktivität zu steigern und Kosten zu minimieren.
Eine MES-Software ist modular strukturiert, so dass der Kunde sich nach Bedarf die einzelnen Funktionsmodule zusammenstellen kann. Unser MES KORVIN 7 MAX besteht z.B. aus folgenden Einzelmodulen:
- BASIS (Basismodul)
- MDE (Maschinendatenerfassung)
- BDE (Betriebsdatenerfassung)
- INST (Instandhaltung)
- ALARM (Alarmierung)
- DOK (Dokumentenmanagement)
- TNT (Traceability)
- PLAN (Feinplanung/Leitstand)
- LOG (Logistik)
- VIS (Visualisierung)
- PEP (Personaleinsatzplanung)
- MPZE (Personalzeiterfassung)
- DNC (Rezepturen/DNC)
- EM (Energiemonitoring)
Aufgabenstellung
Die modulare Struktur und der große Umfang an Modulen ist ein wichtiger Vorteil für unsere Kunden, da Sie nicht so schnell an Grenzen stoßen und sich dann unter Umständen eine weitere Insellösung (extra Software mit extra Datenbank ...) anschaffen müssen.
Wichtig ist, dass die einzelnen Module funktionell ineinandergreifen und alle auf die gleiche Datenbank zugreifen.
Es reicht wenn in der Grafik die Module nur mit er Abkürzung, also z.B. MDE bezeichnet werden. Für den ersten Entwurf können auch Platzhalter genutzt werden.
Der Betrachter sollte aus der Grafik auf den ersten Blick erkennen:
- umfängliches MES
- modular strukturiert
- Funktionsmodule step-by-step erweiterbar
Für die Umsetzung naheliegend wären Puzzle-Steine, Blokkis, ... muss aber nicht.

```html
<!DOCTYPE html>
<html lang="de">
<head>
<meta charset="utf-8">
<title>MES Module</title>
<link rel="stylesheet" href="https://fonts.googleapis.com/css2?family=Source+Sans+3:wght@400;700&display=swap">
<style>
  :root{
    --bg-center:#ffffff;
    --bg-edge:#dde3e6;
    --frame:#1d4a30;
    --hex-rim:#ffffff;
    --connector:#d0d8dc;
    --label:#ffffff;
  }
  html,body{margin:0;padding:0;overflow:hidden;}
  body{width:1200px;height:1050px;}
  .canvas{
    width:1200px;height:1050px;box-sizing:border-box;
    border:1px solid var(--frame);
    background:radial-gradient(ellipse at 50% 45%,var(--bg-center) 0%,#f1f3f4 45%,var(--bg-edge) 100%);
    font-family:"Source Sans 3",sans-serif;
  }
  .honeycomb{display:block;width:1200px;height:1050px;}
  .connector{stroke:var(--connector);stroke-width:11;}
  .rim{fill:var(--hex-rim);}
  .face-top{fill:var(--top);}
  .face-bottom{fill:var(--bottom);}
  .code{fill:var(--label);font-weight:700;font-size:30px;text-anchor:middle;letter-spacing:.5px;}
  .name{fill:var(--label);font-weight:400;font-size:13.5px;text-anchor:middle;}
  .badge{fill:#ffffff;}
  .badge-ring{fill:none;stroke:var(--top);stroke-width:5;}
  .glyph{fill:none;stroke:var(--top);stroke-width:3;stroke-linecap:round;stroke-linejoin:round;}
  .glyph-fill{fill:var(--top);}
  .glyph-knock{fill:#ffffff;}

  .m-basis{--top:#bfcdd5;--bottom:#cbd8de;}
  .m-bde{--top:#f7b000;--bottom:#fbc443;}
  .m-alarm{--top:#e44c17;--bottom:#ec7b3f;}
  .m-mde{--top:#b7cc1f;--bottom:#c8d95c;}
  .m-inst{--top:#ed8200;--bottom:#f29d45;}
  .m-plan{--top:#0f4a2b;--bottom:#2b5f3f;}
  .m-tnt{--top:#62ab25;--bottom:#8abf52;}
  .m-dok{--top:#086934;--bottom:#2e8451;}
  .m-pep{--top:#7ec3ea;--bottom:#a0d3f0;}
  .m-mpze{--top:#069335;--bottom:#4ba959;}
  .m-log{--top:#35245e;--bottom:#5f4781;}
  .m-vis{--top:#2a8ccb;--bottom:#66a7d8;}
  .m-dnc{--top:#6e2e6c;--bottom:#8c5389;}
  .m-em{--top:#1555a0;--bottom:#4b76b4;}
</style>
</head>
<body>
<div class="canvas">
<svg class="honeycomb" viewBox="0 0 1200 1050" xmlns="http://www.w3.org/2000/svg">
  <defs>
    <filter id="lift" x="-20%" y="-20%" width="140%" height="140%">
      <feDropShadow dx="0" dy="3" stdDeviation="5" flood-color="#6b7b84" flood-opacity=".35"/>
    </filter>
    <polygon id="rim-shape" points="-125,0 -62.5,-109 62.5,-109 125,0 62.5,109 -62.5,109"/>
    <polygon id="top-shape" points="-103,1 -51.5,-90 51.5,-90 103,1"/>
    <polygon id="bottom-shape" points="-103,0 103,0 51.5,90 -51.5,90"/>
  </defs>

  <g class="connectors">
    <line class="connector" x1="597" y1="169" x2="597" y2="411"/>
    <line class="connector" x1="597" y1="411" x2="599" y2="653"/>
    <line class="connector" x1="599" y1="653" x2="601" y2="896"/>
    <line class="connector" x1="392" y1="290" x2="392" y2="532"/>
    <line class="connector" x1="392" y1="532" x2="394" y2="775"/>
    <line class="connector" x1="805" y1="290" x2="805" y2="532"/>
    <line class="connector" x1="805" y1="532" x2="807" y2="775"/>
    <line class="connector" x1="186" y1="411" x2="186" y2="653"/>
    <line class="connector" x1="1012" y1="411" x2="1012" y2="653"/>
    <line class="connector" x1="597" y1="169" x2="392" y2="290"/>
    <line class="connector" x1="597" y1="169" x2="805" y2="290"/>
    <line class="connector" x1="392" y1="290" x2="186" y2="411"/>
    <line class="connector" x1="392" y1="290" x2="597" y2="411"/>
    <line class="connector" x1="805" y1="290" x2="597" y2="411"/>
    <line class="connector" x1="805" y1="290" x2="1012" y2="411"/>
    <line class="connector" x1="186" y1="411" x2="392" y2="532"/>
    <line class="connector" x1="597" y1="411" x2="392" y2="532"/>
    <line class="connector" x1="597" y1="411" x2="805" y2="532"/>
    <line class="connector" x1="1012" y1="411" x2="805" y2="532"/>
    <line class="connector" x1="392" y1="532" x2="186" y2="653"/>
    <line class="connector" x1="392" y1="532" x2="599" y2="653"/>
    <line class="connector" x1="805" y1="532" x2="599" y2="653"/>
    <line class="connector" x1="805" y1="532" x2="1012" y2="653"/>
    <line class="connector" x1="186" y1="653" x2="394" y2="775"/>
    <line class="connector" x1="599" y1="653" x2="394" y2="775"/>
    <line class="connector" x1="599" y1="653" x2="807" y2="775"/>
    <line class="connector" x1="1012" y1="653" x2="807" y2="775"/>
    <line class="connector" x1="394" y1="775" x2="601" y2="896"/>
    <line class="connector" x1="807" y1="775" x2="601" y2="896"/>
  </g>

  <!-- BASIS -->
  <g class="module m-basis" transform="translate(597 169)">
    <use href="#rim-shape" class="rim" filter="url(#lift)"/>
    <use href="#top-shape" class="face-top"/><use href="#bottom-shape" class="face-bottom"/>
    <text class="code" x="0" y="-40">BASIS</text><text class="name" x="0" y="-20">Basismodul</text>
    <g transform="translate(0 45)">
      <circle class="badge" r="39"/><circle class="badge-ring" r="33"/>
      <path class="glyph-fill" d="M0 19 C-9 7 -12 0 -12 -6 A12 12 0 0 1 12 -6 C12 0 9 7 0 19Z"/>
      <circle class="glyph-knock" cx="0" cy="-6" r="4.5"/>
    </g>
  </g>

  <!-- BDE -->
  <g class="module m-bde" transform="translate(392 290)">
    <use href="#rim-shape" class="rim" filter="url(#lift)"/>
    <use href="#top-shape" class="face-top"/><use href="#bottom-shape" class="face-bottom"/>
    <text class="code" x="0" y="-40">BDE</text><text class="name" x="0" y="-20">Betriebsdatenerfassung</text>
    <g transform="translate(0 45)">
      <circle class="badge" r="39"/><circle class="badge-ring" r="33"/>
      <path class="glyph" d="M-17 -16 V16 H18 M-11 12 V-6 M-5 12 V-12 M1 12 V0 M11 12 V6"/>
      <circle class="glyph" cx="5" cy="-4" r="7"/><path class="glyph" d="M10 1 L16 8"/>
    </g>
  </g>

  <!-- ALARM -->
  <g class="module m-alarm" transform="translate(805 290)">
    <use href="#rim-shape" class="rim" filter="url(#lift)"/>
    <use href="#top-shape" class="face-top"/><use href="#bottom-shape" class="face-bottom"/>
    <text class="code" x="0" y="-40">ALARM</text><text class="name" x="0" y="-20">Alarmierung</text>
    <g transform="translate(0 45)">
      <circle class="badge" r="39"/><circle class="badge-ring" r="33"/>
      <circle class="glyph-fill" r="5"/>
      <path class="glyph" d="M-9 -9 A13 13 0 0 0 -9 9 M9 -9 A13 13 0 0 1 9 9 M-15 -15 A21 21 0 0 0 -15 15 M15 -15 A21 21 0 0 1 15 15"/>
    </g>
  </g>

  <!-- MDE -->
  <g class="module m-mde" transform="translate(186 411)">
    <use href="#rim-shape" class="rim" filter="url(#lift)"/>
    <use href="#top-shape" class="face-top"/><use href="#bottom-shape" class="face-bottom"/>
    <text class="code" x="0" y="-40">MDE</text><text class="name" x="0" y="-20">Maschinendatenerfassung</text>
    <g transform="translate(0 45)">
      <circle class="badge" r="39"/><circle class="badge-ring" r="33"/>
      <circle class="glyph" cx="-10" cy="-8" r="6" stroke-dasharray="3 2.5" stroke-width="4"/>
      <circle class="glyph" cx="-10" cy="9" r="6" stroke-dasharray="3 2.5" stroke-width="4"/>
      <circle class="glyph" cx="3" cy="-12" r="4" stroke-dasharray="2.5 2" stroke-width="3.5"/>
      <path class="glyph" d="M4 14 L17 -5 L20 -2 L7 17 L3 18 Z"/>
    </g>
  </g>

  <!-- INST -->
  <g class="module m-inst" transform="translate(597 411)">
    <use href="#rim-shape" class="rim" filter="url(#lift)"/>
    <use href="#top-shape" class="face-top"/><use href="#bottom-shape" class="face-bottom"/>
    <text class="code" x="0" y="-40">INST</text><text class="name" x="0" y="-20">Instandhaltung</text>
    <g transform="translate(0 45)">
      <circle class="badge" r="39"/><circle class="badge-ring" r="33"/>
      <path class="glyph" stroke-width="5" d="M-13 13 L8 -8 M13 13 L-8 -8"/>
      <path class="glyph" d="M8 -8 A7 7 0 1 1 16 -14 M-8 -8 L-13 -13 L-16 -10 L-11 -5Z"/>
    </g>
  </g>

  <!-- PLAN -->
  <g class="module m-plan" transform="translate(1012 411)">
    <use href="#rim-shape" class="rim" filter="url(#lift)"/>
    <use href="#top-shape" class="face-top"/><use href="#bottom-shape" class="face-bottom"/>
    <text class="code" x="0" y="-40">PLAN</text><text class="name" x="0" y="-20">Feinplanung/Leitstand</text>
    <g transform="translate(0 45)">
      <circle class="badge" r="39"/><circle class="badge-ring" r="33"/>
      <rect class="glyph" x="-16" y="-13" width="32" height="28" rx="3"/>
      <path class="glyph" d="M-9 -17 V-10 M9 -17 V-10"/>
      <path class="glyph-fill" d="M-11 -4h6v5h-6zM-3 -4h6v5h-6zM5 -4h6v5h-6zM-11 4h6v5h-6zM-3 4h6v5h-6zM5 4h6v5h-6z"/>
    </g>
  </g>

  <!-- TNT -->
  <g class="module m-tnt" transform="translate(392 532)">
    <use href="#rim-shape" class="rim" filter="url(#lift)"/>
    <use href="#top-shape" class="face-top"/><use href="#bottom-shape" class="face-bottom"/>
    <text class="code" x="0" y="-40">TNT</text><text class="name" x="0" y="-20">Traceability</text>
    <g transform="translate(0 45)">
      <circle class="badge" r="39"/><circle class="badge-ring" r="33"/>
      <path class="glyph" stroke-width="4" d="M-17 -9 H-8 C2 -9 2 9 12 9 H15 M-17 9 H-8 C2 9 2 -9 12 -9 H15"/>
      <path class="glyph-fill" d="M13 -15 L20 -9 L13 -3Z M13 3 L20 9 L13 15Z"/>
    </g>
  </g>

  <!-- DOK -->
  <g class="module m-dok" transform="translate(805 532)">
    <use href="#rim-shape" class="rim" filter="url(#lift)"/>
    <use href="#top-shape" class="face-top"/><use href="#bottom-shape" class="face-bottom"/>
    <text class="code" x="0" y="-40">DOK</text><text class="name" x="0" y="-20">Dokumentenmanagement</text>
    <g transform="translate(0 45)">
      <circle class="badge" r="39"/><circle class="badge-ring" r="33"/>
      <path class="glyph" d="M-12 -18 H5 L12 -11 V18 H-12Z M5 -18 V-11 H12"/>
      <path class="glyph" stroke-width="2.5" d="M-7 -3 H7 M-7 3 H7 M-7 9 H7"/>
    </g>
  </g>

  <!-- PEP -->
  <g class="module m-pep" transform="translate(186 653)">
    <use href="#rim-shape" class="rim" filter="url(#lift)"/>
    <use href="#top-shape" class="face-top"/><use href="#bottom-shape" class="face-bottom"/>
    <text class="code" x="0" y="-40">PEP</text><text class="name" x="0" y="-20">Personaleinsatzplanung</text>
    <g transform="translate(0 45)">
      <circle class="badge" r="39"/><circle class="badge-ring" r="33"/>
      <circle class="glyph-fill" cx="-11" cy="-10" r="4"/><circle class="glyph-fill" cx="11" cy="-10" r="4"/>
      <circle class="glyph-fill" cx="0" cy="-7" r="4.5"/>
      <path class="glyph-fill" d="M-17 -4 h12 v12 h-3 v8 h-6 v-8 h-3z M5 -4 h12 v12 h-3 v8 h-6 v-8 h-3z"/>
      <path class="glyph-fill" stroke="#fff" stroke-width="1.5" d="M-7 -1 h14 v13 h-3 v8 h-8 v-8 h-3z"/>
    </g>
  </g>

  <!-- MPZE -->
  <g class="module m-mpze" transform="translate(599 653)">
    <use href="#rim-shape" class="rim" filter="url(#lift)"/>
    <use href="#top-shape" class="face-top"/><use href="#bottom-shape" class="face-bottom"/>
    <text class="code" x="0" y="-40">MPZE</text><text class="name" x="0" y="-20">Personalzeiterfassung</text>
    <g transform="translate(0 45)">
      <circle class="badge" r="39"/><circle class="badge-ring" r="33"/>
      <circle class="glyph" r="19"/>
      <path class="glyph" d="M0 0 L-9 -5 M0 0 L10 -3"/>
      <path class="glyph" stroke-width="2" d="M0 -16 V-13 M0 13 V16 M-16 0 H-13 M13 0 H16"/>
    </g>
  </g>

  <!-- LOG -->
  <g class="module m-log" transform="translate(1012 653)">
    <use href="#rim-shape" class="rim" filter="url(#lift)"/>
    <use href="#top-shape" class="face-top"/><use href="#bottom-shape" class="face-bottom"/>
    <text class="code" x="0" y="-40">LOG</text><text class="name" x="0" y="-20">Logistik</text>
    <g transform="translate(0 45)">
      <circle class="badge" r="39"/><circle class="badge-ring" r="33"/>
      <path class="glyph-fill" d="M-21 -11 H6 V9 H-21Z M8 -5 H15 L21 2 V9 H8Z"/>
      <circle class="glyph-fill" cx="-13" cy="11" r="4.5"/><circle class="glyph-fill" cx="14" cy="11" r="4.5"/>
      <circle class="glyph-knock" cx="-13" cy="11" r="2"/><circle class="glyph-knock" cx="14" cy="11" r="2"/>
    </g>
  </g>

  <!-- VIS -->
  <g class="module m-vis" transform="translate(394 775)">
    <use href="#rim-shape" class="rim" filter="url(#lift)"/>
    <use href="#top-shape" class="face-top"/><use href="#bottom-shape" class="face-bottom"/>
    <text class="code" x="0" y="-40">VIS</text><text class="name" x="0" y="-20">Visualisierung</text>
    <g transform="translate(0 45)">
      <circle class="badge" r="39"/><circle class="badge-ring" r="33"/>
      <path class="glyph" stroke-width="4" d="M-21 0 C-10 -14 10 -14 21 0 C10 14 -10 14 -21 0Z"/>
      <circle class="glyph-fill" r="7"/><circle class="glyph-knock" cx="-2" cy="-2" r="2"/>
    </g>
  </g>

  <!-- DNC -->
  <g class="module m-dnc" transform="translate(807 775)">
    <use href="#rim-shape" class="rim" filter="url(#lift)"/>
    <use href="#top-shape" class="face-top"/><use href="#bottom-shape" class="face-bottom"/>
    <text class="code" x="0" y="-40">DNC</text><text class="name" x="0" y="-20">Rezepturen/DNC</text>
    <g transform="translate(0 45)">
      <circle class="badge" r="39"/><circle class="badge-ring" r="33"/>
      <path class="glyph" d="M0 -9 V-1 M-14 6 V-1 H14 V6 M0 -1 V6"/>
      <path class="glyph-fill" d="M-6 -19 h12 v10 h-12z M-20 6 h12 v10 h-12z M-6 6 h12 v10 h-12z M8 6 h12 v10 h-12z"/>
    </g>
  </g>

  <!-- EM -->
  <g class="module m-em" transform="translate(601 896)">
    <use href="#rim-shape" class="rim" filter="url(#lift)"/>
    <use href="#top-shape" class="face-top"/><use href="#bottom-shape" class="face-bottom"/>
    <text class="code" x="0" y="-40">EM</text><text class="name" x="0" y="-20">Energiemonitoring</text>
    <g transform="translate(0 45)">
      <circle class="badge" r="39"/><circle class="badge-ring" r="33"/>
      <rect class="glyph" stroke-width="3.5" x="-19" y="-10" width="34" height="20" rx="2"/>
      <rect class="glyph-fill" x="17" y="-4" width="4" height="8"/>
      <rect class="glyph-fill" x="-15" y="-6" width="20" height="12"/>
    </g>
  </g>
</svg>
</div>
</body>
</html>
```